Business cards for Harbourline Supply Pty Ltd that import building products into Australia from China
Target Market(s)
Business to Business
Industry/Entity Type
Business
Contact Information for Business Card
Front: Logo and Business Name
Rear:
Desmond Varrick
General Manager
Mobile: 0427 561 394
email: dessie@harbourlinesupply.com.au
alternative email: dessie@outbackworks.com.au
web: www.harbourlinesupply.com.au
Adelaide, Brisbane and Darwin
Colors
ec1f27
fbee3d

```html
<!DOCTYPE html>
<html lang="en">
<head>
<meta charset="utf-8">
<title>Harbourline Supply Pty Ltd — Business Cards</title>
<link href="https://fonts.googleapis.com/css2?family=Montserrat:wght@400;500;700&display=swap" rel="stylesheet">
<style>
  :root {
    --red: #ec1f27;
    --yellow: #fbee3d;
    --black: #050505;
    --white: #ffffff;
    --ink: #333333;
    --backdrop: #2e2e2e;
  }
  * { margin: 0; padding: 0; box-sizing: border-box; }
  html, body {
    width: 1200px; height: 864px; overflow: hidden;
    background: var(--backdrop);
    font-family: "Montserrat", Arial, sans-serif;
  }
  .sheet {
    width: 1200px; height: 864px;
    display: flex; flex-direction: column;
    align-items: center; justify-content: space-evenly;
  }
  .card {
    width: 640px; height: 366px;
    border-radius: 22px;
    position: relative;
    box-shadow: 0 12px 30px rgba(0,0,0,.45);
  }
  /* Front */
  .card--front { background: var(--black); color: var(--white); }
  .brand {
    display: flex; align-items: center; gap: 14px;
  }
  .brand__dot {
    width: 22px; height: 22px; border-radius: 50%; flex: none;
  }
  .brand__name {
    font-weight: 700; color: var(--red);
    line-height: 1.05; text-transform: uppercase; letter-spacing: 1px;
  }
  .card--front .brand {
    position: absolute; left: 50%; top: 44%;
    transform: translate(-50%, -50%);
  }
  .card--front .brand__dot { background: var(--yellow); }
  .card--front .brand__name { font-size: 34px; }
  .cities {
    position: absolute; left: 0; right: 0; bottom: 56px;
    text-align: center; font-size: 15px; font-weight: 500; letter-spacing: .3px;
  }
  .cities__sep {
    display: inline-block; width: 5px; height: 5px; border-radius: 50%;
    background: var(--red); margin: 0 7px; vertical-align: middle;
  }
  /* Back */
  .card--back { background: var(--white); color: var(--ink); }
  .card--back .brand {
    position: absolute; left: 40px; top: 50%; transform: translateY(-50%);
    width: 250px;
  }
  .card--back .brand__dot { background: #3a3a3a; }
  .card--back .brand__name { font-size: 24px; }
  .divider {
    position: absolute; left: 318px; top: 70px; bottom: 70px;
    width: 1.5px; background: var(--red);
  }
  .contact {
    position: absolute; left: 342px; top: 74px; right: 20px;
  }
  .contact__name { color: var(--red); font-weight: 700; font-size: 22px; }
  .contact__role { font-size: 14px; margin: 2px 0 20px 14px; }
  .contact__list { list-style: none; }
  .contact__item {
    display: flex; align-items: center; gap: 9px;
    font-size: 13.5px; line-height: 1.45; margin-left: 14px;
  }
  .contact__icon { width: 13px; height: 13px; flex: none; }
</style>
</head>
<body>
<main class="sheet">
  <section class="card card--front" aria-label="Card front">
    <div class="brand">
      <span class="brand__dot"></span>
      <span class="brand__name">Harbourline Supply<br>Pty Ltd</span>
    </div>
    <p class="cities">Adelaide<span class="cities__sep"></span>Brisbane<span class="cities__sep"></span>Darwin</p>
  </section>

  <section class="card card--back" aria-label="Card back">
    <div class="brand">
      <span class="brand__dot"></span>
      <span class="brand__name">Harbourline Supply<br>Pty Ltd</span>
    </div>
    <div class="divider"></div>
    <div class="contact">
      <p class="contact__name">Desmond Varrick</p>
      <p class="contact__role">General Manager</p>
      <ul class="contact__list">
        <li class="contact__item">
          <svg class="contact__icon" viewBox="0 0 14 14"><rect x="3.5" y="1" width="7" height="12" rx="1.2" fill="none" stroke="#ec1f27" stroke-width="1.4"/><circle cx="7" cy="11" r=".8" fill="#ec1f27"/></svg>
          0427 561 394
        </li>
        <li class="contact__item">
          <svg class="contact__icon" viewBox="0 0 14 14"><rect x="1" y="3" width="12" height="8" fill="#ec1f27"/><path d="M1 3l6 4.5L13 3" fill="none" stroke="#fff" stroke-width="1.2"/></svg>
          dessie@harbourlinesupply.com.au
        </li>
        <li class="contact__item">
          <svg class="contact__icon" viewBox="0 0 14 14"><rect x="1" y="3" width="12" height="8" fill="#ec1f27"/><path d="M1 3l6 4.5L13 3" fill="none" stroke="#fff" stroke-width="1.2"/></svg>
          dessie@outbackworks.com.au
        </li>
        <li class="contact__item">
          <svg class="contact__icon" viewBox="0 0 14 14"><g fill="none" stroke="#ec1f27" stroke-width="1.2"><circle cx="7" cy="7" r="5.8"/><ellipse cx="7" cy="7" rx="2.6" ry="5.8"/><path d="M1.2 7h11.6M2 4h10M2 10h10"/></g></svg>
          www.harbourlinesupply.com.au
        </li>
      </ul>
    </div>
  </section>
</main>
</body>
</html>
```